ELsewhen website redesign to provide information about experiential workshops, film work and other

We need a redesign of our website elsewhen.org. We conduct experiential workshops of discovery and transformation for individuals and organizations. We need the website to reflect the full extent of ELsewhen programs, and be an information hub for ELsewhen workshops and communities as they develop.

The attached documents contain information about the organization - it's brandbook, copy for web pages, a website layout and a couple of images.

The site is for individuals and companies looking to promote and be change to make a difference. It should be warm, welcoming, and create excitement around the concepts and the ability to discover a new way of being in the world. We are about creating communities around the globe who will embody play, freedom, curiosity and expanded possibilities. We are creating a space for this to happen, both physically (workshops) and online.

We will be on either a SquareSpace, but mos tlikely a Weebly plaform.

Please look at the current site at www.elsewhen.org

Target Market(s)

Initially, are target market will be baby boomers, but will expand to include millennials and students.

Coding

Coded - Design and coding required

Number of Pages Required

5+ page

Requirements
Must have
• The colors, logo and fonts from the brand book.
Nice to have
• Complimentary use of brand colors to create an attractive presentation and energy

```html
<!DOCTYPE html>
<html lang="en">
<head>
<meta charset="utf-8">
<title>ELsewhen — Home</title>
<link href="https://fonts.googleapis.com/css2?family=Montserrat:wght@400;500;600;700;800&display=swap" rel="stylesheet">
<style>
:root{
  --ink:#111111;
  --charcoal:#232323;
  --hero-left:#0f0f0f;
  --hero-right:#262626;
  --grey-word:#8a8a8a;
  --nav-bg:#e6e6e6;
  --body-text:#333333;
  --white:#ffffff;
  --placeholder:#d9d9d9;
  --footer-bg:#1d1d1d;
  --footer-text:#a9a9a9;
}
*{box-sizing:border-box;margin:0;padding:0}
html,body{width:1200px;height:2917px;overflow:hidden}
body{font-family:'Montserrat',sans-serif;background:var(--white);color:var(--body-text)}
.wrap{width:936px;margin:0 auto;position:relative}

.site-header{height:91px}
.site-header .wrap{height:91px;display:flex;align-items:center;justify-content:space-between}
.brand{font-weight:700;font-size:36px;letter-spacing:5px;color:var(--charcoal);display:flex;align-items:center;gap:12px}
.brand-mark{width:22px;height:22px;background:var(--charcoal)}
.header-actions{display:flex;gap:8px;margin-top:-6px}
.btn{background:var(--charcoal);color:var(--white);font-size:13px;height:39px;padding:0 18px;display:flex;align-items:center;gap:8px}

.main-nav{background:var(--nav-bg);height:41px}
.main-nav ul{list-style:none;display:flex;justify-content:space-between;height:41px;align-items:center}
.main-nav a{font-size:13px;color:var(--charcoal);text-decoration:none;font-weight:500}
.main-nav a.active{border-bottom:1px solid var(--charcoal)}

.hero{display:flex;height:483px}
.hero-half{width:600px;display:flex;align-items:center}
.hero-half.left{background:var(--hero-left);padding-left:132px}
.hero-half.right{background:var(--hero-right);justify-content:flex-end;padding-right:132px;text-align:right}
.hero h1{font-weight:800;font-size:64px;line-height:67px;color:var(--white);text-transform:uppercase}
.hero h1 em{font-style:normal;color:var(--grey-word)}

.intro{padding-top:55px;height:564px}
.intro h2{font-weight:400;font-size:34px;line-height:43px;text-align:center;color:var(--ink)}
.benefits{display:flex;margin-top:46px;height:299px}
.benefits-list{width:467px;background:var(--charcoal);color:var(--white);padding:36px 0 0 30px}
.benefits-list h3{font-size:18px;font-weight:700;margin-bottom:10px}
.benefits-list li{list-style:none;font-size:15px;height:40px;display:flex;align-items:center;gap:10px}
.photo-ride{width:469px;background:radial-gradient(circle at 60% 40%,#f2c65a 0%,#d8742c 40%,#7a3a2a 75%,#3a2c2a 100%)}

.band{position:relative;color:var(--white);text-align:center}
.band h2{font-weight:400;font-size:33px}
.band p{font-size:15px;line-height:26px;color:#e6e6e6}
.vision{height:327px;background:linear-gradient(180deg,#474747,#2f2f2f);padding-top:71px}
.vision h2{margin-bottom:20px}
.vision p+p{margin-top:24px}
.vision a{color:var(--white)}

.what-we-do{height:451px;padding-top:70px;text-align:center}
.what-we-do h2{font-weight:400;font-size:33px;color:var(--ink);margin-bottom:20px}
.what-we-do p{font-size:15px;line-height:26px}
.what-we-do h3{font-weight:700;font-size:20px;line-height:31px;color:var(--charcoal);margin-top:22px;text-transform:uppercase}
.movements{display:flex;justify-content:center;gap:14px;margin-top:16px}
.movement{width:70px;display:flex;flex-direction:column;align-items:center}
.movement-symbol{width:58px;height:58px;background:var(--placeholder)}
.movement span{font-size:7.5px;font-weight:600;margin-top:5px;white-space:nowrap;color:var(--ink)}

.peace{height:381px;background:linear-gradient(180deg,#3a3a3a,#2b2b2b);padding-top:70px}
.peace h2{margin-bottom:16px}
.peace p+p{margin-top:26px}

.community{height:461px;padding-top:82px}
.community-card{display:flex;height:297px}
.photo-group{width:467px;background:linear-gradient(135deg,#5a5240,#8b7458 50%,#6b5a4a)}
.community-copy{width:469px;background:var(--charcoal);color:var(--white);padding:90px 30px 0}
.community-copy h3{font-size:18px;font-weight:700;margin-bottom:14px}
.community-copy p{font-size:15px;line-height:25px}
.community-copy a{color:var(--white)}

.site-footer{height:118px;background:var(--footer-bg)}
.site-footer .wrap{padding-top:35px}
.footer-links{font-size:11.5px;color:var(--footer-text)}
.footer-links a{color:var(--footer-text);text-decoration:none}
.footer-links i{font-style:normal;margin:0 9px}
.copyright{font-size:11.5px;color:var(--footer-text);margin-top:14px}
.social{position:absolute;right:0;top:47px;display:flex;gap:24px}
.social span{width:14px;height:14px;border-radius:50%;background:var(--footer-text)}
</style>
</head>
<body>
<header class="site-header">
  <div class="wrap">
    <div class="brand"><span class="brand-mark"></span>ELSEWHEN</div>
    <div class="header-actions">
      <span class="btn"><svg width="13" height="10" viewBox="0 0 13 10"><rect width="13" height="10" fill="#fff"/><path d="M0 0l6.5 5L13 0" stroke="#232323" fill="none"/></svg>Newsletter Signup</span>
      <span class="btn"><svg width="12" height="12" viewBox="0 0 12 12"><path d="M0 4h5V1l5 5-5 5V8H0z" fill="#fff"/></svg>Member Login</span>
    </div>
  </div>
</header>

<nav class="main-nav">
  <ul class="wrap">
    <li><a class="active" href="#">HOME</a></li>
    <li><a href="#">ABOUT US</a></li>
    <li><a href="#">WORKSHOPS</a></li>
    <li><a href="#">ELSEWHEN PROJECTS</a></li>
    <li><a href="#">FILMS</a></li>
    <li><a href="#">STORE &amp; RESOURCES</a></li>
    <li><a href="#">COMMUNITY</a></li>
    <li><a href="#">CONTACT US</a></li>
  </ul>
</nav>

<section class="hero">
  <div class="hero-half left"><h1>What<br>world do<br><em>we</em> want<br>to live in?</h1></div>
  <div class="hero-half right"><h1>What kind<br>of life do<br><em>you</em> want<br>to create?</h1></div>
</section>

<section class="intro">
  <div class="wrap">
    <h2>Discover an Opportunity to Live a<br>More Dynamic and Meaningful Life</h2>
    <div class="benefits">
      <div class="benefits-list">
        <h3>ELSEWHEN :</h3>
        <ul>
          <li><svg width="13" height="11" viewBox="0 0 13 11"><path d="M1 6l4 4 7-9" stroke="#fff" stroke-width="2.4" fill="none"/></svg>Moves Energy</li>
          <li><svg width="13" height="11" viewBox="0 0 13 11"><path d="M1 6l4 4 7-9" stroke="#fff" stroke-width="2.4" fill="none"/></svg>Creates Opportunities for Connecting</li>
          <li><svg width="13" height="11" viewBox="0 0 13 11"><path d="M1 6l4 4 7-9" stroke="#fff" stroke-width="2.4" fill="none"/></svg>Supports Conscious Evolution</li>
          <li><svg width="13" height="11" viewBox="0 0 13 11"><path d="M1 6l4 4 7-9" stroke="#fff" stroke-width="2.4" fill="none"/></svg>Deepens Experience of Life</li>
          <li><svg width="13" height="11" viewBox="0 0 13 11"><path d="M1 6l4 4 7-9" stroke="#fff" stroke-width="2.4" fill="none"/></svg>Provides Opportunities for Collaboration and Creation</li>
        </ul>
      </div>
      <div class="photo-ride" role="img" aria-label="Photo of a joyful couple on a spinning fairground swing ride, motion-blurred"></div>
    </div>
  </div>
</section>

<section class="band vision" role="img" aria-label="Background photo of a busy city street crowd, darkened">
  <div class="wrap">
    <h2>Vision</h2>
    <p>We envision a world in which all people and communities can challenge and break free from stories that no longer serve us. We believe that solutions to contemporary challenges will emerge from a place of curiosity, love and connection.</p>
    <p>Through inspiration, conscious reflection, and collaboration, we take responsibility for the world we are manifesting, and we can discover and create new possibilities for the lives and the society we desire to <a href="#">build</a>.</p>
  </div>
</section>

<section class="what-we-do">
  <div class="wrap">
    <h2>What We Do</h2>
    <p>ELsewhen Life is a workshop designed to re-engage you with life. Through interactive exercises and personal exploration, you are taken on a journey that ultimately leaves you experiencing life as a Creator. You will learn to see beliefs and patterns that hold you back in work and relationships as well as a path to transforming the story of your life.</p>
    <h3>ELsewhen Life is a 2-3 day workshop<br>experienced in 5 movements:</h3>
    <div class="movements">
      <div class="movement"><div class="movement-symbol" role="img" aria-label="Symbol for the Curiosity movement"></div><span>Curiosity</span></div>
      <div class="movement"><div class="movement-symbol" role="img" aria-label="Symbol for the Awareness movement"></div><span>Awareness</span></div>
      <div class="movement"><div class="movement-symbol" role="img" aria-label="Symbol for the Owning Your Creation movement"></div><span>Owning Your Creation</span></div>
      <div class="movement"><div class="movement-symbol" role="img" aria-label="Symbol for the Reimagining movement"></div><span>Reimagining</span></div>
      <div class="movement"><div class="movement-symbol" role="img" aria-label="Symbol for the Manifesting movement"></div><span>Manifesting</span></div>
    </div>
  </div>
</section>

<section class="band peace" role="img" aria-label="Background photo of a street protest with placards, darkened">
  <div class="wrap">
    <h2>Unsettling the Calm</h2>
    <p>The Unsettling the Calm workshop—an extension of the documentary of the same name—is an experiential process to transform participants into disturbers of the status quo within themselves, to enhance their relationships with others, and to change the environments in which they exist—and ultimately society—for the better.</p>
    <p>This workshop experience challenges us all to understand the narratives we live within, to look at our current roles in society, and to decide what role we will play to create a more humane, just and peaceful world, for all. It all starts with our willingness to disturb the “peace” of the status quo.</p>
  </div>
</section>

<section class="community">
  <div class="wrap">
    <div class="community-card">
      <div class="photo-group" role="img" aria-label="Photo of a workshop group sitting together on a striped rug in a wooden room"></div>
      <div class="community-copy">
        <h3>IN YOUR COMMUNITY</h3>
        <p>Bring ELsewhen or the Unsettling the Calm workshop to your community. We would love to hear from you. Please fill out the brief form <a href="#">here</a></p>
      </div>
    </div>
  </div>
</section>

<footer class="site-footer">
  <div class="wrap">
    <div class="footer-links"><a href="#">Home</a><i>|</i><a href="#">About Us</a><i>|</i><a href="#">Workshops</a><i>|</i><a href="#">ELsewhen Projects</a><i>|</i><a href="#">Films</a><i>|</i><a href="#">Store &amp; Resources</a><i>|</i><a href="#">Community</a><i>|</i><a href="#">Contact Us</a></div>
    <div class="copyright">Copyright © 2018 ELsewhen. All rights reserved.</div>
    <div class="social" aria-label="Social links"><span></span><span></span><span></span></div>
  </div>
</footer>
</body>
</html>
```